Post it Note design

POST-IT NOTE DESIGN (CONTENT)
Size recommended: 4x6 for handwriting space.
Header (Bold):
Lighting Issue Detected on Your Property
Sub-header:
During our routine night inspection, we noted the following item(s):
Checkbox List:
⬜ Building Lights Out
⬜ Pole Lights Out
⬜ Sign Not Illuminated
⬜ Other ________________________
Action Line:
We can provide a quote or dispatch service right away.
Area for notes
Contact Block (Bold & Centered):
Lumaveil Fixture Inc.
Service@LumaveilFixture.com
www.LumaveilFixture.com
877-514-6028
Industry/Entity Type
Electrical lighting
Colors
Designer to choose colors to be used in the design.
Look and feel
Each slider illustrates characteristics of the customer's brand and the style your logo design should communicate.

```html
<!DOCTYPE html>
<html lang="en">
<head>
<meta charset="utf-8">
<title>Lighting Issue Detected – Lumaveil Fixture Inc.</title>
<link rel="stylesheet" href="https://fonts.googleapis.com/css2?family=Montserrat:ital,wght@0,400;0,600;0,700;0,800;1,600&family=Lato:wght@400;700&display=swap">
<style>
  :root {
    --page-bg: #f4f4f6;
    --note-bg: #ffffff;
    --header-bg: #ededee;
    --ink: #1f2124;
    --navy: #2b3445;
    --lime: #c5dc3a;
    --muted: #8a8b8d;
    --brand-red: #d6202c;
    --field-bg: #f1f1f2;
    --notes-bg: #f7f7f9;
    --notes-border: #d5d8de;
    --dots: #9aa7bd;
    --action-bg: #c4dbf1;
    --footer-bg: #232a35;
    --white: #ffffff;
  }
  * { box-sizing: border-box; margin: 0; padding: 0; }
  html, body { width: 1200px; height: 1137px; overflow: hidden; }
  body {
    background: var(--page-bg);
    font-family: "Lato", Arial, sans-serif;
    color: var(--ink);
    position: relative;
  }
  .note {
    position: absolute;
    left: 266px; top: 83px;
    width: 659px; height: 988px;
    background: var(--note-bg);
    box-shadow: 0 2px 10px rgba(0,0,0,0.12);
    overflow: hidden;
  }
  .note > * { position: absolute; }

  .note-header {
    left: 0; top: 0; width: 100%; height: 192px;
    background: var(--header-bg);
  }
  .brand-name {
    left: 36px; top: 62px; width: 200px;
    font-family: "Montserrat", sans-serif;
    font-weight: 800; font-size: 27px; line-height: 1.1;
    color: var(--brand-red);
    text-align: center;
  }
  .headline {
    left: 262px; top: 0; width: 366px; height: 192px;
    text-align: center;
    font-family: "Montserrat", sans-serif;
  }
  .headline-top {
    display: block; margin-top: 30px;
    font-weight: 700; font-size: 40px; line-height: 1.1;
    color: var(--ink); letter-spacing: 0.5px;
  }
  .headline-flag {
    display: block; width: 340px; height: 45px; margin: 8px auto 0;
    background: var(--navy); color: var(--lime);
    font-weight: 800; font-size: 38px; line-height: 45px; letter-spacing: 1px;
  }
  .headline-sub {
    display: block; margin-top: 4px;
    font-weight: 400; font-size: 35px; line-height: 1.15;
    color: var(--muted); letter-spacing: 0.5px;
  }

  .field {
    top: 221px; width: 289px; height: 41px;
    border: 2px solid var(--navy);
    background: var(--field-bg);
    font-size: 21px; line-height: 37px; padding-left: 36px;
    color: var(--navy);
  }
  .field-date { left: 33px; }
  .field-time { left: 333px; padding-left: 28px; }

  .intro {
    left: 32px; top: 282px; width: 600px;
    font-size: 21px; line-height: 1.28; color: #2c2e31;
  }

  .checklist { left: 33px; top: 358px; width: 600px; list-style: none; }
  .checklist li {
    display: flex; align-items: center;
    height: 46px;
    font-size: 27px; font-weight: 700; color: #2a2c30;
  }
  .checkbox {
    width: 27px; height: 27px; margin-right: 16px; flex: none;
    border: 2.5px solid var(--navy); border-radius: 5px;
  }
  .other-line {
    flex: 1; margin: 10px 34px 0 8px;
    border-bottom: 2px dotted var(--dots);
  }

  .notes-area {
    left: 37px; top: 557px; width: 590px; height: 146px;
    background: var(--notes-bg);
    border: 1.5px solid var(--notes-border);
    padding: 32px 25px 0;
    display: grid; grid-template-columns: 1fr 1fr; column-gap: 8px; row-gap: 40px;
    align-content: start;
  }
  .notes-area span { border-bottom: 2px dotted var(--dots); height: 0; }

  .action-line {
    left: 36px; top: 717px; width: 588px; height: 45px;
    background: var(--action-bg);
    text-align: center; font-size: 20px; line-height: 45px; color: #1f2124;
  }
  .action-line strong { font-weight: 700; }

  .call-prompt {
    left: 30px; top: 810px;
    font-family: "Montserrat", sans-serif;
    font-style: italic; font-weight: 600; font-size: 28px;
    color: var(--brand-red);
  }

  .contact-bar {
    left: 0; top: 852px; width: 100%; height: 136px;
    background: var(--footer-bg);
  }
  .service-photo {
    left: 355px; top: 782px; width: 304px; height: 206px;
    background: linear-gradient(135deg, #e8eaed 0%, #b9bcc2 35%, #4a515c 65%, #2b323d 100%);
    opacity: 0.9;
  }
  .contact-block { left: 18px; top: 870px; width: 340px; color: var(--white); }
  .phone {
    display: flex; align-items: center;
    font-family: "Montserrat", sans-serif;
    font-weight: 700; font-size: 35px; color: var(--lime);
    line-height: 46px;
  }
  .phone svg { width: 36px; height: 36px; margin-right: 10px; }
  .contact-line { display: block; font-size: 21px; line-height: 26px; padding-left: 2px; }
  .contact-line:first-of-type { margin-top: 4px; }
</style>
</head>
<body>
  <main class="note">
    <div class="note-header"></div>
    <div class="brand-name">Lumaveil Fixture Inc.</div>
    <h1 class="headline">
      <span class="headline-top">LIGHTING ISSUE</span>
      <span class="headline-flag">DETECTED</span>
      <span class="headline-sub">on Your Property</span>
    </h1>

    <div class="field field-date">DATE:</div>
    <div class="field field-time">TIME:</div>

    <p class="intro">During our routine night inspection, we noted the following item(s):</p>

    <ul class="checklist">
      <li><span class="checkbox"></span>Building Lights Out</li>
      <li><span class="checkbox"></span>Pole Lights Out</li>
      <li><span class="checkbox"></span>Sign Not Illuminated</li>
      <li><span class="checkbox"></span>Other:<span class="other-line"></span></li>
    </ul>

    <div class="notes-area" aria-label="Notes">
      <span></span><span></span>
      <span></span><span></span>
      <span></span><span></span>
    </div>

    <p class="action-line">We can provide a <strong>quote or dispatch service</strong> right away.</p>

    <p class="call-prompt">Call Us Today</p>

    <div class="contact-bar"></div>
    <div class="service-photo" role="img" aria-label="Bucket truck service vehicle and parking lot pole light fixtures"></div>
    <div class="contact-block">
      <div class="phone">
        <svg viewBox="0 0 36 36" aria-hidden="true">
          <circle cx="18" cy="18" r="16" fill="none" stroke="#c5dc3a" stroke-width="2.5"/>
          <path d="M12.5 10.5l3 0.2 1.3 4-2 1.6c1 2.2 2.6 3.8 4.8 4.8l1.6-2 4 1.3 0.2 3c-0.5 1.3-1.8 2-3.2 1.8-6-1-10.5-5.5-11.5-11.5-0.2-1.4 0.5-2.7 1.8-3.2z" fill="#c5dc3a"/>
          <path d="M20 9.5a7 7 0 0 1 6.5 6.5M20 13a3.5 3.5 0 0 1 3 3" fill="none" stroke="#c5dc3a" stroke-width="1.6" stroke-linecap="round"/>
        </svg>
        877-514-6028
      </div>
      <span class="contact-line">Service@LumaveilFixture.com</span>
      <span class="contact-line">www.LumaveilFixture.com</span>
    </div>
  </main>
</body>
</html>
```